Business Cards used to invite people to our church

We are a church and have need of a business card sized advertisement that allows our members to hand them out in order to invite people to the church. I need the front of the card to say "You're Invited" or "Come Check us out". with the service times on the back of the card later.
I have attached one of the OLD cards we have used in the past, but we want a complete makeover, into a more modern style that does not require the image.
I am also replacing the old logo with a newer "flat" logo which is attached.
Please use marketing colors. (blue or red or something that catches attention)
Create a card that DOES NOT have the picture of the two people on the front
The information on the sample card back is correct to go onto new card
Target Market(s)
anyone
Industry/Entity Type
Business
Contact Information for Business Card
sertice times and address information which you can get from the sample card I uploaded. It should have "You're Invited" or "Come Check us out" on the front of the card with out logo.

```html
<!DOCTYPE html>
<html lang="en">
<head>
<meta charset="utf-8">
<title>Grace Harbor – Invitation Card</title>
<link rel="stylesheet" href="https://fonts.googleapis.com/css2?family=Open+Sans:wght@400;600;700&display=swap">
<style>
  :root {
    --page-bg: #e9e6e1;
    --navy-deep: #0b1f5c;
    --navy: #1a3f9c;
    --sky: #2f6fd0;
    --cyan: #1aa4e0;
    --cyan-light: #3ec0ee;
    --red: #e8222e;
    --white: #ffffff;
    --ink: #0a1638;
  }
  * { box-sizing: border-box; margin: 0; padding: 0; }
  html, body {
    width: 1200px; height: 913px; overflow: hidden;
    background: var(--page-bg);
    font-family: "Open Sans", Arial, sans-serif;
  }
  .canvas {
    position: relative; width: 1200px; height: 913px;
    display: flex; align-items: center; justify-content: center; gap: 60px;
  }
  .card {
    position: relative; width: 525px; height: 300px;
    overflow: hidden; border-radius: 4px;
    box-shadow: 0 10px 24px rgba(0,0,0,.25);
  }
  .card__art {
    position: absolute; inset: 0;
    background:
      radial-gradient(ellipse at 70% 35%, rgba(120,160,235,.55), transparent 60%),
      radial-gradient(ellipse at 25% 75%, rgba(90,130,220,.45), transparent 55%),
      linear-gradient(160deg, var(--navy-deep) 0%, var(--navy) 50%, var(--sky) 100%);
  }

  /* Front */
  .brand {
    position: absolute; top: 46px; right: 70px;
    display: flex; align-items: center; gap: 12px;
    color: var(--white); font-weight: 700; font-size: 34px; letter-spacing: 1px;
    text-transform: uppercase;
  }
  .brand__dot { width: 20px; height: 20px; border-radius: 50%; background: var(--white); }
  .headline {
    position: absolute; right: 40px; bottom: 62px;
    font-size: 34px; font-weight: 400; letter-spacing: 1px;
    color: var(--white); text-transform: uppercase;
  }
  .headline__accent { color: var(--red); font-weight: 600; }

  /* Back */
  .back__lower {
    position: absolute; left: 0; right: 0; top: 118px; bottom: 0;
    background: linear-gradient(180deg, var(--cyan-light) 0%, var(--cyan) 55%, #1578c8 100%);
    border-top: 4px solid var(--red);
  }
  .contact {
    position: absolute; top: 26px; right: 32px; left: 150px;
    color: var(--white); font-size: 12.5px; font-weight: 600; letter-spacing: .6px;
    text-transform: uppercase; text-align: right; line-height: 1.9;
  }
  .contact__phone { padding-right: 6px; }
  .schedule {
    position: absolute; left: 36px; right: 32px; top: 144px;
    list-style: none; color: var(--ink);
    font-size: 14px; font-weight: 700; text-transform: uppercase; letter-spacing: .5px;
  }
  .schedule__row { display: flex; align-items: baseline; margin-bottom: 20px; }
  .schedule__leader { flex: 1; border-bottom: 2px dotted var(--ink); margin: 0 6px; transform: translateY(-4px); }
  .schedule__time { font-weight: 600; }
</style>
</head>
<body>
<main class="canvas">
  <section class="card card--front" aria-label="Card front">
    <div class="card__art" role="img" aria-label="Deep blue cloudy sky with white doves in flight, one carrying an olive branch"></div>
    <div class="brand"><span class="brand__dot"></span>Grace Harbor</div>
    <h1 class="headline">You’re <span class="headline__accent">Invited</span></h1>
  </section>

  <section class="card card--back" aria-label="Card back">
    <div class="card__art" role="img" aria-label="Blue cloudy sky with white doves in flight"></div>
    <div class="back__lower"></div>
    <address class="contact">
      <div>www.graceharbor.org</div>
      <div>A: 420 W. Cedar Lane - Millbrook, TX 75990</div>
      <div class="contact__phone">P: 1-800-555-0142</div>
    </address>
    <ul class="schedule">
      <li class="schedule__row"><span>Sunday</span><span class="schedule__leader"></span><span class="schedule__time">9:00 AM</span></li>
      <li class="schedule__row"><span>Sunday</span><span class="schedule__leader"></span><span class="schedule__time">11: AM</span></li>
      <li class="schedule__row"><span>Wed. Bible Class</span><span class="schedule__leader"></span><span class="schedule__time">7:00 PM</span></li>
    </ul>
  </section>
</main>
</body>
</html>
```